New web design for a service provider in the medical field

We are looking for a new design for our website. We are a company that repairs and sells medical endoscopes. Our customers include doctors and hospitals. Our current website can be found at https://lumavex.de/en/lumavex-english.
We need a new web design (without programming) for the following 3 pages:
-Startpage https://lumavex.de/en/lumavex-english/
-Used endoscopes https://lumavex.de/en/used-endoscopes/
-Purchase https://lumavex.de/en/purchase/
The design should be modern and stylish.
The blue color of the logo should be reflected on the page, but not too intrusive.
I have uploaded the images from the header. If more images are needed, let me know and I will upload them.

Target Market(s)
Doctors and hospitals

```html
<!DOCTYPE html>
<html lang="en">
<head>
<meta charset="utf-8">
<title>Lumavex – Endoscope Repair and Sale</title>
<link href="https://fonts.googleapis.com/css2?family=Poppins:wght@400;500;600;700;800&display=swap" rel="stylesheet">
<style>
:root{
  --blue:#2a8fd8;
  --blue-deep:#1673c4;
  --blue-soft:#cfe3f1;
  --ink:#1d1d1f;
  --muted:#555;
  --dark:#141414;
  --navy:#0d3b7a;
  --red:#d8202a;
  --white:#fff;
}
*{box-sizing:border-box;margin:0;padding:0}
html,body{width:1200px;height:4975px;overflow:hidden}
body{position:relative;font-family:"Poppins",sans-serif;color:var(--ink);background:var(--white)}
.abs{position:absolute}
.btn{position:absolute;display:flex;align-items:center;justify-content:center;font-weight:600;font-size:13px;text-transform:uppercase;border-radius:3px}
.btn-blue{background:var(--blue);color:var(--white)}
.btn-white{background:var(--white);color:var(--blue)}
.photo{position:absolute}

/* header */
.site-header{position:absolute;left:0;top:0;width:1200px;height:115px;background:var(--white)}
.brand{position:absolute;display:flex;align-items:center;gap:10px;font-weight:700;color:var(--ink)}
.brand-dot{width:14px;height:14px;border-radius:50%;background:var(--blue)}
.contact-line{position:absolute;top:18px;display:flex;align-items:center;gap:8px;font-size:14px}
.contact-line .ic{width:26px;height:26px;border-radius:50%;background:var(--blue);display:flex;align-items:center;justify-content:center}
.main-nav{position:absolute;top:72px;left:303px;display:flex;gap:32px;font-size:15px}
.main-nav .active{color:var(--blue);border-bottom:2px solid var(--blue);padding-bottom:10px}

/* hero */
.hero-photo{left:0;top:115px;width:1200px;height:650px;background:linear-gradient(100deg,#e8f3f6 0%,#cde5ea 40%,#a9cfd9 70%,#7fb3c2 100%)}
.hero-title{left:110px;top:305px;font-size:40px;line-height:52px;font-weight:800;color:var(--blue-deep);text-transform:uppercase}
.hero-text{left:110px;top:430px;width:560px;font-size:15px;line-height:27px}

.section-title{position:absolute;left:0;width:1200px;text-align:center;font-weight:700;color:var(--blue);text-transform:uppercase}

/* service */
.brand-tag{position:absolute;top:960px;height:45px;display:flex;align-items:center;justify-content:center;color:var(--white);font-weight:700;font-size:16px}
.card{position:absolute;top:1050px;height:420px;border-radius:14px;background:var(--white);box-shadow:0 2px 10px rgba(0,0,0,.12);text-align:center}
.card.featured{background:var(--blue);color:var(--white)}
.card .circle{position:absolute;left:50%;top:35px;width:112px;height:112px;margin-left:-56px;border-radius:50%;background:var(--blue);display:flex;align-items:center;justify-content:center}
.card.featured .circle{background:var(--white)}
.card h3{position:absolute;left:0;right:0;top:170px;font-size:20px;color:var(--blue);font-weight:700}
.card.featured h3{color:var(--white)}
.card h4{position:absolute;left:0;right:0;top:203px;font-size:17px;font-weight:500}
.card p{position:absolute;left:30px;right:30px;top:240px;font-size:12.5px;line-height:21px}
.card .btn{left:50%;width:120px;margin-left:-60px;top:342px;height:38px}

/* about */
.about-band{left:0;top:1640px;width:1200px;height:600px;background:var(--blue-soft)}
.about-frame{left:110px;top:1925px;width:457px;height:168px;background:var(--blue);border-radius:6px}
.about-photo{left:128px;top:1578px;width:420px;height:492px;border-radius:6px;background:linear-gradient(160deg,#e6e9ec,#b9c3cb 55%,#8799a8)}
.about-title{left:638px;top:1693px;font-size:28px;font-weight:700;color:var(--blue)}
.about-lead{left:638px;top:1742px;width:450px;font-size:17px;line-height:29px;font-weight:500}
.about-text{left:638px;top:1805px;width:450px;font-size:14.5px;line-height:24px;text-align:justify;color:#333}

/* decision */
.feature{position:absolute;width:300px}
.feature h5{font-size:18px;font-weight:600;color:var(--blue);line-height:24px}
.feature p{font-size:12px;line-height:19px;margin-top:5px;color:#333}
.feature.left{text-align:right}
.feature.left p{margin-left:auto}
.feat-icon{position:absolute;width:80px;height:80px;border-radius:50%;background:var(--white);box-shadow:0 2px 10px rgba(0,0,0,.13);display:flex;align-items:center;justify-content:center}

/* faulty */
.surgery-photo{left:0;top:3020px;width:1200px;height:700px;background:linear-gradient(180deg,#0e2c52,#3a6590 45%,#1a3b61)}
.faulty-box{left:110px;top:3418px;width:980px;height:302px;background:var(--blue);color:var(--white);text-align:center}

/* news */
.news{position:absolute;overflow:hidden}
.news .date{position:absolute;background:var(--blue);color:var(--white);font-size:11px;padding:4px 14px}
.news .cap{position:absolute;color:var(--white);font-weight:500}

/* footer */
.footer{left:0;top:4500px;width:1200px;height:475px;background:var(--dark);color:var(--white)}
.footer h6{position:absolute;font-size:18px;font-weight:600}
.footer .links{position:absolute;font-size:15px;line-height:32px}
.social{position:absolute;top:4620px;width:26px;height:26px;border-radius:50%;background:var(--blue)}
.field{position:absolute;left:780px;width:310px;height:44px;background:var(--white);border-radius:3px;color:#222;font-size:14px;padding:12px 16px}
</style>
</head>
<body>

<header class="site-header">
  <div class="brand" style="left:105px;top:42px;font-size:22px"><span class="brand-dot"></span>Lumavex</div>
  <div class="contact-line" style="left:583px">
    <span class="ic"><svg width="14" height="11" viewBox="0 0 14 11"><rect x="1" y="1" width="12" height="9" fill="none" stroke="#fff" stroke-width="1.5"/><path d="M1 1l6 5 6-5" fill="none" stroke="#fff" stroke-width="1.5"/></svg></span>info@lumavex.de
  </div>
  <div class="contact-line" style="left:818px">
    <span class="ic"><svg width="13" height="13" viewBox="0 0 24 24"><path d="M6 2l4 5-2 3c1 3 3 5 6 6l3-2 5 4-3 4C10 21 3 14 2 5z" fill="#fff"/></svg></span>+49 4021 555 187-0
  </div>
  <div class="contact-line" style="left:1026px;font-size:13px">
    <svg width="18" height="18" viewBox="0 0 20 20"><circle cx="10" cy="10" r="8" fill="none" stroke="#333" stroke-width="1.5"/><ellipse cx="10" cy="10" rx="3.5" ry="8" fill="none" stroke="#333" stroke-width="1.3"/><path d="M2 10h16" stroke="#333" stroke-width="1.3"/></svg>⌄ EN
  </div>
  <nav class="main-nav">
    <span class="active">Home</span><span>About</span><span>Endoscope Repair</span><span>Endoscopy Systems</span><span>Endoscopy Accessories</span><span>Purchase</span>
  </nav>
</header>

<section class="hero">
  <div class="photo hero-photo" role="img" aria-label="Doctor holding a flexible endoscope in an operating room"></div>
  <h1 class="abs hero-title">Put your endoscope in<br>reliable hands!</h1>
  <p class="abs hero-text">Lumavex Gmbh Is Specialised In The Repair And Sale Of Aurelis, Kestra And Norvane Flexible Medical Endoscopes.</p>
  <div class="btn btn-blue" style="left:110px;top:510px;width:134px;height:44px">Get started</div>
  <svg class="abs" style="left:0;top:660px" width="1200" height="110" viewBox="0 0 1200 110" preserveAspectRatio="none">
    <path d="M0 90C250 20 450 40 650 70S1050 60 1200 10V110H0Z" fill="var(--blue)"/>
    <path d="M0 110C250 45 460 60 660 85S1050 70 1200 35V110Z" fill="#fff"/>
  </svg>
</section>

<section class="service">
  <h2 class="section-title" style="top:833px;font-size:28px">Your future - our service</h2>
  <p class="abs" style="left:120px;top:880px;width:960px;text-align:center;font-size:14.5px;line-height:25px">Lumavex GmbH is specialised in the repair and sale of Aurelis, Kestra and Norvane flexible medical endoscopes. As a service-oriented company, we are at your side with our knowledge and skills!</p>
  <div class="brand-tag" style="left:397px;width:125px;background:var(--navy)">AURELIS</div>
  <div class="brand-tag" style="left:536px;width:128px;background:var(--red)">KESTRA</div>
  <div class="brand-tag" style="left:676px;width:128px;background:#000">NORVANE</div>

  <article class="card" style="left:110px;width:313px">
    <div class="circle"><svg width="60" height="60" viewBox="0 0 60 60"><path d="M12 48L40 20M20 12l28 28" stroke="#fff" stroke-width="7" stroke-linecap="round"/></svg></div>
    <h3>Repair</h3><h4>Endoscope repair service</h4>
    <p>Manufacturer-independent we repair and maintain endoscopes, individual components (e.g. processors or light sources).</p>
    <div class="btn btn-blue">Read more</div>
  </article>
  <article class="card featured" style="left:446px;width:310px;border-radius:14px 14px 20px 20px">
    <div class="circle"><svg width="60" height="60" viewBox="0 0 60 60"><circle cx="36" cy="30" r="15" fill="none" stroke="var(--blue)" stroke-width="4"/><text x="36" y="37" text-anchor="middle" font-size="20" font-weight="700" fill="var(--blue)" font-family="Poppins,sans-serif">$</text><path d="M6 22h12M6 30h10M6 38h12" stroke="var(--blue)" stroke-width="4"/></svg></div>
    <h3>Sale</h3><h4>Endoscope repair service</h4>
    <p>Our regular stock includes refurbished gastroscopes, coloscopes, bronchoscopes, cystoscopes and duodenoscopes</p>
    <div class="btn btn-white">Read more</div>
  </article>
  <article class="card" style="left:776px;width:314px">
    <div class="circle"><svg width="60" height="60" viewBox="0 0 60 60"><path d="M10 28l20-8 20 8-20 8z" fill="#fff"/><path d="M12 32v14l18 8V40zM48 32v14l-18 8V40z" fill="#fff"/><circle cx="30" cy="14" r="9" fill="#fff"/><path d="M26 14l3 3 5-6" stroke="var(--blue)" stroke-width="2.5" fill="none"/></svg></div>
    <h3>Purchase</h3><h4>Used endoscopes</h4>
    <p>We are very interested in buying your old endoscopes – even defective and dismantled! We offer fair conditions!</p>
    <div class="btn btn-blue">Read more</div>
  </article>
</section>

<section class="about">
  <div class="abs about-band"></div>
  <svg class="abs" style="left:0;top:2190px" width="1200" height="80" viewBox="0 0 1200 80" preserveAspectRatio="none">
    <path d="M0 50C300 0 500 20 700 40S1050 30 1200 0V80H0Z" fill="var(--blue)"/>
    <path d="M0 70C300 20 500 40 700 60S1050 45 1200 20V80H0Z" fill="#fff"/>
  </svg>
  <div class="abs about-frame"></div>
  <div class="photo about-photo" role="img" aria-label="Technician handling an endoscope at a video processor tower"></div>
  <h2 class="abs about-title">ABOUT US</h2>
  <p class="abs about-lead">Endoscope repairs and second hand endoscopes from Lumavex – cause the outcome matters!</p>
  <p class="abs about-text">Lumavex is a privileged partner for the start-up facility or optimisation of existing healthcare facilities, doctor's offices and hospitals. The quality and reliability of our products and our offered service are our best advertisement!As a result of optimised processes and highly qualified specialists in our company, we can work very quickly and with high quality for your benefit of least possible restrictions in your doctor's office or in your hospital.</p>
  <div class="btn btn-blue" style="left:637px;top:2040px;width:120px;height:38px">Read more</div>
</section>

<section class="decision">
  <h2 class="section-title" style="top:2350px;font-size:28px;line-height:40px">Lumavex GmbH,<br>your decision for your future</h2>
  <svg class="abs" style="left:390px;top:2530px" width="420" height="420" viewBox="0 0 420 420">
    <circle cx="210" cy="210" r="198" fill="none" stroke="#333" stroke-width="2.5" stroke-dasharray="9 6"/>
    <circle cx="210" cy="210" r="160" fill="#fff" stroke="#eee" stroke-width="6"/>
    <g fill="var(--blue)" stroke="#fff" stroke-width="3">
      <circle cx="91" cy="52" r="11"/><circle cx="329" cy="52" r="11"/>
      <circle cx="12" cy="170" r="11"/><circle cx="408" cy="170" r="11"/>
      <circle cx="59" cy="333" r="11"/><circle cx="361" cy="333" r="11"/>
    </g>
  </svg>
  <div class="brand abs" style="left:500px;top:2712px;font-size:26px"><span class="brand-dot"></span>Lumavex</div>

  <div class="feature left" style="left:50px;top:2495px"><h5>First Class Service</h5><p>Our clients always come first!</p></div>
  <div class="feature left" style="left:0;top:2640px;width:276px"><h5>Loan Equipment Service</h5><p style="max-width:230px">Use our service of high-quality loan devices during the downtime of your</p></div>
  <div class="feature left" style="left:0;top:2805px"><h5>Highly Cost Efficient</h5><p style="max-width:170px">Benefit from our first class recommendations and</p></div>
  <div class="feature" style="left:846px;top:2495px"><h5>Fast Repairs</h5><p style="max-width:220px">Keep potential disruptions in your doctor's office or in your</p></div>
  <div class="feature" style="left:926px;top:2640px;width:240px"><h5>On-Site Service</h5><p>We will gladly pay you a visit to to carry out analysis and repairs on site.</p></div>
  <div class="feature" style="left:882px;top:2805px;width:250px"><h5>Without A Maintenance Contract</h5><p>No subscription or other maintenance contract, but one-time and</p></div>

  <div class="feat-icon" style="left:366px;top:2505px"><svg width="40" height="40" viewBox="0 0 40 40" fill="var(--blue)"><circle cx="20" cy="12" r="5"/><circle cx="9" cy="16" r="4"/><circle cx="31" cy="16" r="4"/><path d="M10 32c0-7 20-7 20 0zM2 30c0-5 10-6 10 0zM28 30c0-6 10-5 10 0z"/></svg></div>
  <div class="feat-icon" style="left:748px;top:2505px"><svg width="40" height="40" viewBox="0 0 40 40"><circle cx="20" cy="22" r="12" fill="none" stroke="var(--blue)" stroke-width="3"/><path d="M20 22v-7M17 6h6" stroke="var(--blue)" stroke-width="3"/></svg></div>
  <div class="feat-icon" style="left:288px;top:2654px"><svg width="40" height="40" viewBox="0 0 40 40"><rect x="8" y="5" width="24" height="30" rx="2" fill="none" stroke="var(--blue)" stroke-width="3"/><path d="M13 14h14M13 21h14M13 28h9" stroke="var(--blue)" stroke-width="2.5"/></svg></div>
  <div class="feat-icon" style="left:826px;top:2654px"><svg width="40" height="40" viewBox="0 0 40 40"><circle cx="20" cy="20" r="15" fill="none" stroke="var(--blue)" stroke-width="3"/><path d="M20 11v9l6 4" stroke="var(--blue)" stroke-width="3" fill="none"/></svg></div>
  <div class="feat-icon" style="left:338px;top:2818px"><svg width="40" height="40" viewBox="0 0 40 40"><path d="M4 14h12M4 22h10M4 30h12M12 4l-4 5h8z" stroke="var(--blue)" stroke-width="3" fill="var(--blue)"/><circle cx="27" cy="24" r="9" fill="var(--blue)"/></svg></div>
  <div class="feat-icon" style="left:782px;top:2818px"><svg width="40" height="40" viewBox="0 0 40 40"><path d="M8 32L28 12M12 8l20 20" stroke="var(--blue)" stroke-width="5" stroke-linecap="round"/></svg></div>
</section>

<section class="faulty">
  <div class="photo surgery-photo" role="img" aria-label="Surgical team in caps and masks working under operating lights"></div>
  <div class="abs faulty-box">
    <h2 style="margin-top:66px;font-size:28px;font-weight:700">FAULTY ENDOSCOPE?</h2>
    <p style="margin-top:22px;font-size:15px">We ensure quick and smooth repairs!</p>
    <p style="margin-top:14px;font-size:19px;font-weight:600">Simple place a</p>
    <div class="btn btn-white" style="left:409px;top:200px;width:162px;height:38px">Pick-up order</div>
  </div>
  <div class="abs" style="left:0;top:3716px;width:1200px;height:6px;background:var(--blue)"></div>
</section>

<section class="news-section">
  <h2 class="section-title" style="top:3785px;font-size:28px">Cause the outcome matters!</h2>
  <article class="news" style="left:110px;top:3888px;width:473px;height:477px" role="img" aria-label="Doctor and colleague discussing in a hospital corridor">
    <div class="photo" style="inset:0;background:linear-gradient(150deg,#e9eef2,#a4b6c4 50%,#3b4f63)"></div>
    <span class="date" style="left:36px;bottom:78px;font-size:13px">05 AUGUST 2022</span>
    <span class="cap" style="left:36px;bottom:30px;font-size:20px;font-weight:600">One Company For Everyone</span>
  </article>
  <article class="news" style="left:598px;top:3888px;width:239px;height:232px" role="img" aria-label="Surgeon holding an endoscope">
    <div class="photo" style="inset:0;background:linear-gradient(160deg,#eef2f5,#8ba5bf 55%,#2a3f5c)"></div>
    <span class="date" style="left:30px;bottom:46px">05 AUGUST 2022</span>
    <span class="cap" style="left:26px;bottom:16px;font-size:12px">Experience Characterises Us</span>
  </article>
  <article class="news" style="left:850px;top:3888px;width:238px;height:232px" role="img" aria-label="Empty hospital ward with beds">
    <div class="photo" style="inset:0;background:linear-gradient(160deg,#c9d6e2,#7e96ae 55%,#2c3f55)"></div>
    <span class="date" style="left:30px;bottom:46px">05 AUGUST 2022</span>
    <span class="cap" style="left:26px;bottom:16px;font-size:12px">The Product Is Close To Our Hearts</span>
  </article>
  <article class="news" style="left:598px;top:4133px;width:239px;height:232px" role="img" aria-label="Operating room monitors and equipment">
    <div class="photo" style="inset:0;background:linear-gradient(160deg,#5b7390,#2b3d57 55%,#121c2b)"></div>
    <span class="date" style="left:30px;bottom:46px">05 AUGUST 2022</span>
    <span class="cap" style="left:26px;bottom:16px;font-size:12px">Guaranteed Service</span>
  </article>
  <article class="news" style="left:850px;top:4133px;width:238px;height:232px" role="img" aria-label="Smiling medical team">
    <div class="photo" style="inset:0;background:linear-gradient(160deg,#f1f1f1,#b9a594 55%,#3e3a3a)"></div>
    <span class="date" style="left:30px;bottom:46px">05 AUGUST 2022</span>
    <span class="cap" style="left:26px;bottom:16px;font-size:12px">Quality Not Quantity</span>
  </article>
</section>

<footer>
  <svg class="abs" style="left:0;top:4440px" width="1200" height="62" viewBox="0 0 1200 62" preserveAspectRatio="none">
    <path d="M0 20C250 55 500 55 750 35S1050 0 1200 5V62H0Z" fill="var(--blue)"/>
    <path d="M0 40C250 62 500 62 750 48S1050 20 1200 25V62H0Z" fill="var(--dark)"/>
  </svg>
  <div class="abs footer">
    <div class="brand" style="left:105px;top:80px;font-size:20px;color:#fff"><span class="brand-dot"></span>Lumavex</div>
    <h6 style="left:110px;top:172px">Contact Us</h6>
    <div class="abs" style="left:110px;top:222px;font-size:14px;line-height:22px;display:flex;gap:18px">
      <svg width="20" height="20" viewBox="0 0 20 20"><circle cx="10" cy="10" r="10" fill="var(--blue)"/><path d="M10 4a4 4 0 014 4c0 3-4 8-4 8s-4-5-4-8a4 4 0 014-4z" fill="#fff"/></svg>
      <span>Lindenweg 12, 24107<br>Talheim Germany</span>
    </div>
    <div class="abs" style="left:110px;top:282px;font-size:14px;display:flex;gap:18px;align-items:center">
      <svg width="20" height="20" viewBox="0 0 20 20"><circle cx="10" cy="10" r="10" fill="var(--blue)"/><rect x="5" y="6.5" width="10" height="7" fill="none" stroke="#fff" stroke-width="1.3"/></svg>info@lumavex.de
    </div>
    <div class="abs" style="left:110px;top:326px;font-size:14px;display:flex;gap:18px;align-items:center">
      <svg width="20" height="20" viewBox="0 0 20 20"><circle cx="10" cy="10" r="10" fill="var(--blue)"/><path d="M7 5l2 3-1 1.5c.6 1.4 1.6 2.4 3 3L12.5 11l3 2-1.5 2C10 15 5 10 5 6z" fill="#fff"/></svg>+49 4021 555 187-0
    </div>
    <h6 style="left:372px;top:68px">Quick&nbsp; LINKS</h6>
    <div class="links" style="left:373px;top:98px">Home<br>About<br>Endoscope Repair<br>Endoscopy Systems<br>Endoscopy Accessories<br>Purchase</div>
    <h6 style="left:553px;top:68px">Follow LINKS</h6>
    <h6 style="left:776px;top:68px">How Can We Help You?</h6>
    <div class="field" style="top:114px">Email</div>
    <div class="field" style="top:170px">Password</div>
    <div class="btn btn-blue" style="left:780px;top:228px;width:310px;height:44px;font-size:14px">Subscribe</div>
    <div class="abs" style="left:0;width:1200px;top:432px;text-align:center;font-size:11px">COPYRIGHTS © LUMAVEX | ALL RIGHTS RESERVED.</div>
  </div>
  <span class="social" style="left:563px"></span>
  <span class="social" style="left:607px"></span>
  <span class="social" style="left:651px"></span>
  <span class="social" style="left:695px"></span>
</footer>

</body>
</html>
```